Book Cover Design - "Lanterns Beneath Orchards"

Looking for an eye-catching but professional book cover.

This book is designed to help people figure out why they hate their job and what to do about it.

The audience for this book is 18-35 year olds who feel stuck in their current roles. The theory here is that people often wind up in a job they don't love, then settle because they don't realize they can make things better.

The writer's style is clever and balances humor with practical advice.

```html
<!DOCTYPE html>
<html lang="en">
<head>
<meta charset="utf-8">
<title>Lanterns Beneath Orchards — Book Cover</title>
<link rel="stylesheet" href="https://fonts.googleapis.com/css2?family=Anton&family=Courier+Prime&family=Libre+Baskerville:wght@700&display=swap">
<style>
  :root {
    --page: #ffffff;
    --cover-ink: #0b1821;
    --band: #231f20;
    --title-top: #ffd400;
    --title-bottom: #f68b1f;
    --byline: #d9d9d9;
    --spine-byline: #ffffff;
  }
  * { box-sizing: border-box; margin: 0; padding: 0; }
  html, body {
    width: 1200px;
    height: 1000px;
    overflow: hidden;
    background: var(--page);
  }
  .canvas {
    width: 1200px;
    height: 1000px;
    display: flex;
    align-items: center;
    justify-content: center;
  }
  .book {
    width: 630px;
    height: 800px;
    display: block;
  }
  .title-word {
    font-family: "Anton", "Oswald", sans-serif;
    text-transform: uppercase;
  }
  .byline {
    font-family: "Courier Prime", "Courier New", monospace;
    font-size: 20px;
    fill: var(--byline);
    letter-spacing: 1px;
  }
  .spine-title {
    font-family: "Anton", "Oswald", sans-serif;
    font-size: 30px;
    text-transform: uppercase;
  }
  .spine-byline {
    font-family: "Libre Baskerville", "Georgia", serif;
    font-weight: 700;
    font-size: 18px;
    fill: var(--spine-byline);
  }
</style>
</head>
<body>
<main class="canvas">
  <svg class="book" viewBox="0 0 630 800" xmlns="http://www.w3.org/2000/svg" aria-labelledby="book-title">
    <title id="book-title">Lanterns Beneath Orchards, by writer name</title>
    <defs>
      <linearGradient id="title-gradient" x1="0" y1="0" x2="0" y2="1">
        <stop offset="0" stop-color="var(--title-top)"/>
        <stop offset="1" stop-color="var(--title-bottom)"/>
      </linearGradient>
      <linearGradient id="spine-gradient" x1="0" y1="0" x2="1" y2="0">
        <stop offset="0" stop-color="var(--title-bottom)"/>
        <stop offset="1" stop-color="var(--title-top)"/>
      </linearGradient>
    </defs>

    <g class="spine">
      <rect x="0" y="0" width="70" height="800" fill="var(--cover-ink)"/>
      <text class="spine-title" transform="translate(35,24) rotate(90)" x="0" y="13" fill="url(#spine-gradient)" textLength="430" lengthAdjust="spacingAndGlyphs">Lanterns Beneath Orchards</text>
      <text class="spine-byline" transform="translate(35,640) rotate(90)" x="0" y="6">by writer name</text>
    </g>

    <g class="front-cover" transform="translate(70,0)">
      <rect class="cover-ground" x="0" y="0" width="560" height="800" fill="var(--cover-ink)"/>

      <g class="cover-figures" role="img" aria-label="Silhouettes of three figures walking, two holding hands, one carrying a flower">
        <rect x="110" y="60" width="340" height="250" rx="6" fill="url(#title-gradient)" opacity="0.85"/>
      </g>

      <g class="cover-title" fill="url(#title-gradient)">
        <text class="title-word" x="285" y="465" font-size="150" text-anchor="middle" textLength="520" lengthAdjust="spacingAndGlyphs">Lanterns</text>
        <text class="title-word" x="300" y="610" font-size="150" text-anchor="middle" textLength="480" lengthAdjust="spacingAndGlyphs">Beneath</text>
        <text class="title-word" x="285" y="796" font-size="150" text-anchor="middle" textLength="520" lengthAdjust="spacingAndGlyphs">Orchards</text>
      </g>

      <g class="author-band">
        <rect x="60" y="620" width="500" height="44" fill="var(--band)"/>
        <text class="byline" x="310" y="648" text-anchor="middle">by writer name</text>
      </g>
    </g>
  </svg>
</main>
</body>
</html>
```